International oil and gas consultancy business needs a web design

Hello, I need a web design for a new oil and gas auditing consultancy business. My business undertakes contract audit assignments to review past costs of oil and gas operations (see attached Excel file for more details of the businesses services). I need the design to give the impression of a professional consultancy style of business, rather than a retail style of website. Note: this job is for LAYOUT DESIGN ONLY and not coding / development work.
The following are my key design principles:
1. BASIC DESIGN: I am after a simple and static web design. I don't want the pages busy or cluttered with too many images or detail.
2. HORIZONTAL TABS: I require a horizontal set of tabs towards the top of the screens (see Excel file) which remain in the same position on every page.
3. META TAG PLANNING: The design should allow for effective positioning of content so that key meta tag words can easily be built during the technical build stage.
4. NUMBER OF PAGES: The site will eventually have a maximum of 10 pages. Seven of the pages will reside under the tabs. Can you please present your opening submission for the first two page.
5. USE OF MY LOGO: The attached logo (JPEG file) should be used throughout the website. Please don't change the shape and colour.
6. COLOUR SCHEMES: Can you please consider any of the 3 colour schemes below:
A - dark red (to match the logo), light grey and perhaps another of your liking;
B - dark red (to match the logo), light cream and perhaps another of your liking;
C - dark red (to match the logo), white and perhaps another of your liking.
7. WORD CONTENT: I have attached an Excel file which shows the estimated word content for each page.
8. FUTURE USE OF DESIGN: I'm planning on building a Wordpress website. Can you please ensure the layout design supports this application.

Target Market(s)

oil and gas companies (small and large)

Industry/Entity Type

Oil And Gas

Font styles to use
Sans Serif

Requirements
Nice to have
• The KRL logo and business name should ideally be next to each other. Also, the logo and name should be part of the background graphics, not above it.

```html
<!DOCTYPE html>
<html lang="en">
<head>
<meta charset="utf-8">
<title>KRL — Kestrel Resource Ledger</title>
<link rel="stylesheet" href="https://fonts.googleapis.com/css2?family=Cabin:wght@600;700&family=Open+Sans:wght@400;600&display=swap">
<style>
  :root {
    --brand-red: #8e1b21;
    --nav-text: #333333;
    --body-grey: #7a7a7a;
    --white: #ffffff;
    --panel-white: rgba(255, 255, 255, 0.82);
    --footer-top: #5a5d62;
    --footer-bottom: #050505;
    --hero-light: #c9ccd3;
    --hero-mid: #8f97a8;
    --hero-dark: #4f596d;
    --card-shade: rgba(25, 25, 25, 0.55);
  }
  * { box-sizing: border-box; margin: 0; padding: 0; }
  html, body { width: 1200px; height: 689px; overflow: hidden; background: var(--white); }
  body { position: relative; font-family: "Open Sans", Arial, sans-serif; color: var(--nav-text); }

  .site-header { position: absolute; left: 0; top: 0; width: 1200px; height: 113px; background: var(--white); }
  .brand { position: absolute; left: 180px; top: 4px; color: var(--brand-red); font-family: "Open Sans", Arial, sans-serif; font-weight: 600; }
  .brand-mark { display: block; font-size: 58px; line-height: 70px; letter-spacing: 6px; }
  .brand-name { display: block; font-size: 14.5px; letter-spacing: 1.2px; margin-top: 2px; }

  .social { position: absolute; top: 28px; left: 885px; display: flex; gap: 14px; }
  .social span { width: 24px; height: 24px; border-radius: 3px; display: block; }
  .social .feed { background: #f2b01e; }
  .social .micro { background: #7fc6ee; }
  .social .shots { background: #e086b4; }
  .social .book { background: #3b5a9a; }

  .main-nav { position: absolute; top: 79px; left: 435px; display: flex; font-size: 11.3px; }
  .main-nav a { color: var(--nav-text); text-decoration: none; position: relative; padding-bottom: 6px; }
  .main-nav a + a { margin-left: 39px; }
  .main-nav a.current::after { content: ""; position: absolute; left: 0; right: 0; bottom: 0; height: 2px; background: var(--brand-red); }

  .header-rule { position: absolute; top: 113px; left: 0; width: 1200px; height: 4px; background: var(--brand-red); }

  .hero { position: absolute; top: 117px; left: 0; width: 1200px; height: 483px; overflow: hidden; }
  .hero-photo { position: absolute; inset: 0; background: linear-gradient(120deg, var(--hero-light) 0%, #b3b8c4 35%, var(--hero-mid) 60%, #c2c5cc 85%, #9aa0ac 100%); }

  .intro-panel { position: absolute; left: 181px; top: 94px; width: 426px; height: 156px; background: var(--panel-white); padding: 22px 14px 0 15px; }
  .intro-title { font-family: "Cabin", Arial, sans-serif; font-weight: 600; font-size: 17px; color: var(--brand-red); letter-spacing: 0.2px; }
  .intro-text { margin-top: 12px; font-size: 12.2px; line-height: 17.2px; color: var(--body-grey); }

  .slide-arrow { position: absolute; top: 217px; width: 26px; height: 50px; }
  .slide-arrow.prev { left: 105px; }
  .slide-arrow.next { left: 1046px; }

  .services-heading { position: absolute; left: 180px; top: 288px; font-family: "Cabin", Arial, sans-serif; font-weight: 600; font-size: 16.5px; color: var(--white); letter-spacing: 0.2px; }

  .service-cards { position: absolute; left: 180px; top: 330px; display: flex; gap: 10px; }
  .service-card { position: relative; width: 274px; height: 138px; overflow: hidden; text-align: right; padding: 36px 14px 0 0; color: var(--white); }
  .service-photo { position: absolute; inset: 0; }
  .service-card:nth-child(1) .service-photo { background: linear-gradient(90deg, #dfe2e8 0%, #8c93a2 45%, #2c2c2e 100%); }
  .service-card:nth-child(2) .service-photo { background: linear-gradient(90deg, #3b3f48 0%, #6d6f78 40%, #2a2a2c 100%); }
  .service-card:nth-child(3) .service-photo { background: linear-gradient(90deg, #5d6a85 0%, #a9afba 40%, #2d2d2f 100%); }
  .service-card::before { content: ""; position: absolute; inset: 0; background: linear-gradient(90deg, rgba(0,0,0,0) 30%, var(--card-shade) 70%); }
  .service-title, .service-text { position: relative; }
  .service-title { font-weight: 600; font-size: 12.3px; letter-spacing: 0.2px; }
  .service-text { margin-top: 10px; font-size: 11px; line-height: 15.5px; color: #d6d6d6; }

  .site-footer { position: absolute; top: 600px; left: 0; width: 1200px; height: 89px; background: linear-gradient(180deg, var(--footer-top) 0%, #1c1d1f 55%, var(--footer-bottom) 100%); color: var(--white); font-size: 11px; text-align: center; }
  .footer-nav { padding-top: 27px; }
  .footer-nav a, .legal a { color: var(--white); text-decoration: none; }
  .footer-nav .sep { margin: 0 8px; }
  .legal { margin-top: 6px; }
  .legal .bar { margin: 0 7px; }
</style>
</head>
<body>
  <header class="site-header">
    <div class="brand">
      <span class="brand-mark">KRL</span>
      <span class="brand-name">Kestrel Resource Ledger</span>
    </div>
    <div class="social" aria-label="Social links">
      <span class="feed"></span><span class="micro"></span><span class="shots"></span><span class="book"></span>
    </div>
    <nav class="main-nav">
      <a class="current" href="#">Home</a>
      <a href="#">About us</a>
      <a href="#">Services</a>
      <a href="#">Our patners</a>
      <a href="#">Approach</a>
      <a href="#">Why choose us</a>
      <a href="#">Contact us</a>
    </nav>
  </header>
  <div class="header-rule"></div>

  <section class="hero">
    <div class="hero-photo" role="img" aria-label="Business meeting photo: hands over a tablet and printed financial charts on a desk"></div>

    <div class="intro-panel">
      <h1 class="intro-title">KESTREL RESOURCE LEDGER</h1>
      <p class="intro-text">&nbsp;is a Perth (Australia) based firm specialising in providing quality audit services for the oil and gas industry. Our skills and knowledge of oil and gas, along with a deep understanding of business commercial needs, ensures the high quality of our services</p>
    </div>

    <svg class="slide-arrow prev" viewBox="0 0 26 50" aria-label="Previous slide"><polyline points="25,1 1,25 25,49" fill="none" stroke="#ffffff" stroke-width="1.3"/></svg>
    <svg class="slide-arrow next" viewBox="0 0 26 50" aria-label="Next slide"><polyline points="1,1 25,25 1,49" fill="none" stroke="#ffffff" stroke-width="1.3"/></svg>

    <h2 class="services-heading">KESTREL RESOURCE LEDGER SPECIALISE IN THE FOLLOWING SERVICES</h2>

    <div class="service-cards">
      <article class="service-card">
        <div class="service-photo" role="img" aria-label="Photo of a hand with a pen reviewing printed charts"></div>
        <h3 class="service-title">JOIN VENTURE AUDITS</h3>
        <p class="service-text">Sed ut perspiciatis<br>undeomnis iste natus error<br>sit voluptatem accusa</p>
      </article>
      <article class="service-card">
        <div class="service-photo" role="img" aria-label="Photo of a businessman gesturing over a report during a meeting"></div>
        <h3 class="service-title">CONTRACT AUDITS</h3>
        <p class="service-text">Sed ut perspiciatis<br>undeomnis iste natus error<br>sit voluptatem accusa</p>
      </article>
      <article class="service-card">
        <div class="service-photo" role="img" aria-label="Photo of a business handshake"></div>
        <h3 class="service-title">OPERATION AUIDITS</h3>
        <p class="service-text">Sed ut perspiciatis<br>undeomnis iste natus error<br>sit voluptatem accusa</p>
      </article>
    </div>
  </section>

  <footer class="site-footer">
    <nav class="footer-nav">
      <a href="#">Home</a><span class="sep">/</span>
      <a href="#">About us</a><span class="sep">/</span>
      <a href="#">Service</a><span class="sep">/</span>
      <a href="#">Our Partners</a><span class="sep">/</span>
      <a href="#">Approach</a><span class="sep">/</span>
      <a href="#">Why Choose us</a><span class="sep">/</span>
      <a href="#">Contact us</a>
    </nav>
    <p class="legal">Copyright © 2014 Kestrel Resource Ledger.&nbsp;&nbsp; <a href="#">Terms and Conditions</a><span class="bar">|</span><a href="#">Privacy policy</a></p>
  </footer>
</body>
</html>
```